Brovanek Data Yellow rose letterhead

I have a new logo for my company but in its current form it is too large to be used on letterhead or as a email signature. I need to have the designer use elements from the current logo and create something close to the original but more suited for smaller items.
Updates

I just uploaded a copy of our logo that does not have the weathered affect. Thanks

Reason: More time for revisions

Industry/Entity Type

It Company

Requirements
Must have
• The design must maintain the visual effect of the current logo. It needs to include the yellow rose and the name of the company.
Nice to have
• It would be nice to maintain the stamp theme and incorporate my name, address, phone, email. etc.

```html
<!DOCTYPE html>
<html lang="en">
<head>
<meta charset="utf-8">
<title>Brovanek Data Letterhead</title>
<link href="https://fonts.googleapis.com/css2?family=Poiret+One&display=swap" rel="stylesheet">
<style>
  :root {
    --paper: #bdb8b5;
    --frame: #f7d46a;
    --teal: #3bbcc0;
    --rule: #5a4a44;
    --rose: #f6c93a;
    --rose-light: #fde27a;
  }
  * { margin: 0; padding: 0; box-sizing: border-box; }
  html, body { width: 772px; height: 1200px; overflow: hidden; background: var(--paper); }
  .letterhead {
    position: relative;
    width: 772px;
    height: 1200px;
    background: var(--paper);
    border: 4px solid var(--frame);
    border-left-width: 6px;
    font-family: "Poiret One", sans-serif;
    color: var(--teal);
  }
  .brand-mark {
    position: absolute;
    left: 32px;
    top: 22px;
    width: 126px;
    height: 126px;
  }
  .company-name {
    position: absolute;
    left: 178px;
    top: 6px;
    font-size: 66px;
    font-weight: 400;
    letter-spacing: 6px;
    line-height: 1.1;
    white-space: nowrap;
  }
  .header-rule {
    position: absolute;
    left: 181px;
    top: 76px;
    width: 540px;
    height: 2px;
    background: var(--rule);
  }
  .footer-rule {
    position: absolute;
    left: 8px;
    top: 1047px;
    width: 747px;
    height: 2px;
    background: var(--rule);
  }
  .contact {
    position: absolute;
    left: 16px;
    top: 1056px;
    list-style: none;
    font-size: 25px;
    font-weight: 400;
    letter-spacing: 3.5px;
    line-height: 25.6px;
    white-space: nowrap;
  }
</style>
</head>
<body>
  <main class="letterhead">
    <svg class="brand-mark" viewBox="0 0 126 126" role="img" aria-label="Yellow rose emblem">
      <defs>
        <radialGradient id="rose-fill" cx="50%" cy="45%" r="55%">
          <stop offset="0%" stop-color="var(--rose-light)"/>
          <stop offset="100%" stop-color="var(--rose)"/>
        </radialGradient>
      </defs>
      <circle cx="63" cy="63" r="60" fill="url(#rose-fill)"/>
    </svg>
    <h1 class="company-name">Brovanek Data</h1>
    <div class="header-rule"></div>

    <div class="footer-rule"></div>
    <ul class="contact">
      <li class="contact-name">Mara Vellin, PhD</li>
      <li class="contact-street">418 NE Cedar Bluff Trail, STE 2107</li>
      <li class="contact-city">Pine Hollow, TX 75312</li>
      <li class="contact-email">Mara@brovanek-data.com</li>
      <li class="contact-phone">1-800-555-0148</li>
    </ul>
  </main>
</body>
</html>
```